Business Card Design for Marketing Firm

Looking for business card design for higher end marketing firm. Clean but impressionable/trendy. We are a marketing firm that represents manufacturers in the foodservice equipment and supply industry. Our customers are end users such has hotels, restaurants, country clubs, convention centers and casinos as well as distributors of restaurants supplies and equipment, and manufacturers of foodservice equipment and supplies.
Target Market(s)
Hotels, Restaurants, Supply & Equipment Distributors, Foodservice Manufacturers
Industry/Entity Type
Foodservice/Hospitality
Contact Information for Business Card
Name, Title, Contact Number, Email, Website, Social Media, Address
Requirements
Must have
- Clean & Simple but Serious and Impressionable

```html
<!DOCTYPE html>
<html lang="en">
<head>
<meta charset="utf-8">
<title>Meridian Foodservice Reps – Business Card</title>
<link rel="stylesheet" href="https://fonts.googleapis.com/css2?family=Marcellus&family=Montserrat:wght@700&family=Open+Sans:wght@400&display=swap">
<style>
  :root {
    --navy: #2a2a78;
    --white: #ffffff;
    --ink: #4a4a55;
    --backdrop: #e8e7ee;
    --card-w: 540px;
    --card-h: 309px;
  }
  * { box-sizing: border-box; margin: 0; padding: 0; }
  html, body {
    width: 1200px; height: 834px; overflow: hidden;
    background: var(--backdrop);
  }
  .stage {
    position: relative; width: 1200px; height: 834px;
  }
  .card {
    position: absolute; top: 262px;
    width: var(--card-w); height: var(--card-h);
    overflow: hidden;
    box-shadow: 0 6px 18px rgba(20, 20, 60, 0.18);
  }
  .card--contact { left: 40px; background: var(--white); }
  .card--brand { left: 620px; background: var(--navy); }

  .wave { position: absolute; inset: 0; width: 100%; height: 100%; }

  .company {
    position: absolute;
    font-family: "Marcellus", serif;
    letter-spacing: 0.04em;
    line-height: 1.1;
    text-align: right;
  }
  .card--contact .company {
    right: 34px; top: 210px;
    font-size: 20px; color: var(--navy);
  }
  .card--brand .company {
    left: 0; right: 0; top: 118px;
    margin: 0 auto; width: 390px;
    font-size: 27px; color: var(--white);
  }
  .company__line { display: block; white-space: nowrap; }

  .person {
    position: absolute; left: 34px; top: 108px;
  }
  .person__name {
    font-family: "Montserrat", sans-serif;
    font-weight: 700; font-size: 17px;
    color: var(--navy); letter-spacing: 0.02em;
  }
  .person__title {
    font-family: "Open Sans", sans-serif;
    font-size: 12px; color: var(--ink);
    margin-top: 2px;
  }
  .contact-list {
    list-style: none; margin-top: 14px;
    font-family: "Open Sans", sans-serif;
    font-size: 12px; color: var(--ink);
  }
  .contact-list li {
    display: flex; align-items: center; gap: 7px;
    height: 19px;
  }
  .contact-list svg { width: 11px; height: 11px; flex: none; }

  .address {
    position: absolute; left: 300px; top: 262px;
    font-family: "Open Sans", sans-serif;
    font-size: 12px; line-height: 1.4; color: var(--ink);
  }
</style>
</head>
<body>
<main class="stage">

  <section class="card card--contact" aria-label="Business card, contact side">
    <svg class="wave" viewBox="0 0 540 309" aria-hidden="true">
      <path fill="var(--navy)" d="M0 0 H540 V200 C450 185 395 160 345 105 C290 40 190 20 0 42 Z"/>
      <path fill="none" stroke="var(--white)" stroke-width="3" d="M120 0 C225 8 300 35 352 90 C405 148 465 172 540 180"/>
      <path fill="none" stroke="var(--white)" stroke-width="2" d="M200 0 C280 14 335 42 375 85 C420 135 475 158 540 164"/>
    </svg>

    <div class="person">
      <div class="person__name">DANIEL PORTER</div>
      <div class="person__title">Managing Director</div>
      <ul class="contact-list">
        <li>
          <svg viewBox="0 0 12 12" aria-hidden="true"><path fill="var(--navy)" d="M2.3 1 4 0.6 5.2 3.3 4 4.2c.6 1.4 1.5 2.3 2.8 2.9l.9-1.2 2.7 1.2-.4 1.7C9.7 9.6 8.7 10 7.6 9.7 4.6 8.8 2.6 6.7 1.9 3.8 1.7 2.8 1.9 1.8 2.3 1z"/></svg>
          123 456 789
        </li>
        <li>
          <svg viewBox="0 0 12 12" aria-hidden="true"><rect x="0.5" y="2" width="11" height="8" rx="1" fill="var(--navy)"/><path d="M1 2.8 6 6.5 11 2.8" fill="none" stroke="var(--white)" stroke-width="1"/></svg>
          info@youremail.com
        </li>
        <li>
          <svg viewBox="0 0 12 12" aria-hidden="true"><circle cx="6" cy="6" r="5.5" fill="var(--navy)"/><path d="M0.8 6H11.2M6 0.5C3.8 3 3.8 9 6 11.5M6 0.5C8.2 3 8.2 9 6 11.5" fill="none" stroke="var(--white)" stroke-width="0.8"/></svg>
          www.yourwebsite.com
        </li>
      </ul>
    </div>

    <h2 class="company">
      <span class="company__line">MERIDIAN FOODSERVICE</span>
      <span class="company__line">REPS</span>
    </h2>

    <address class="address" style="font-style: normal;">
      Your address, City<br>State, Zip 1234
    </address>
  </section>

  <section class="card card--brand" aria-label="Business card, brand side">
    <h1 class="company">
      <span class="company__line">MERIDIAN FOODSERVICE</span>
      <span class="company__line">REPS</span>
    </h1>
  </section>

</main>
</body>
</html>
```